Business Cards for new orthopaedic surgery practice

My husband and I are starting our own orthopaedic surgery practice. We are looking for a business card that is uniform, but one will have my name/title and the other will have his. You can just create one design with my name on it for now. But when I choose your design as the winning design I will ask that you add another copy with his name/title.

We are looking for classy, simple, elite all in one. We like dark blues/a little gold/yellow. Something that goes with our logo. We want our logo incorporated. Here is all the info you need:
Business name: RV Bone & Vitality Center
Location: 38517 North Willowmere Ave
Maple Harbor, FL 33958
Phone: 954-218-4063
Fax: 954-582-7341
Email: info@myrvbonecare.example

Names: Lydia Vance, M.D.
Board Certified Hand and Upper Extremity Surgeon

Ebo Dansu, M.D.
Board Certified Hip & Knee Replacement/General Orthopaedic Surgeon

Can decide what you want to put on the back. Maybe a slogan:
Steady Hands. Lasting Motion

I am just going to upload our logo. The only thing is if we select you as the winning design, the location, and phone numbers may change. We will need your help to update that once fully solidified.

Industry/Entity Type

Medical

Contact Information for Business Card

Colors
0054AA
0677BA
7BADD7
CADEEF
E8F1F8
0094D4
00A9DD
6FCCEA
C7EBF8
E9F6FB

Requirements
Must have
• class, appeal,
Should not have
• We want to air on the side of masculine if we are looking at masculine vs. feminine feel. But we still want it classy, sophisticated, and something we will love

```html
<!DOCTYPE html>
<html lang="en">
<head>
<meta charset="utf-8">
<title>RV Bone &amp; Vitality Center – Business Card</title>
<link rel="stylesheet" href="https://fonts.googleapis.com/css2?family=Cinzel:wght@600;700&family=Arimo:wght@400&display=swap">
<style>
  :root {
    --navy: #1f2f5c;
    --navy-deep: #1b2a55;
    --navy-top: #263966;
    --gold: #c4a25e;
    --ink: #3a3d44;
    --rule: #d6d6d6;
    --paper: #ffffff;
    --backdrop: #e4e4e4;
    --faint: #f4f5f7;
  }
  * { box-sizing: border-box; margin: 0; padding: 0; }
  html, body { width: 1200px; height: 1200px; overflow: hidden; }
  body { background: var(--backdrop); position: relative; font-family: "Arimo", Arial, sans-serif; }

  .card { position: absolute; left: 160px; width: 880px; height: 500px; overflow: hidden; }
  .card-front { top: 80px; background: var(--paper); }
  .card-back { top: 640px; background: linear-gradient(180deg, var(--navy-top), var(--navy-deep)); }

  .front-decor { position: absolute; left: 0; top: 0; }

  .brand-mark {
    position: absolute; display: flex; align-items: center; justify-content: center;
    border-radius: 50%; text-align: center;
    font-family: "Cinzel", serif; font-weight: 700; letter-spacing: 2px; line-height: 1.35;
  }
  .card-front .brand-mark { left: 613px; top: 60px; width: 210px; height: 210px; border: 2px solid var(--gold); color: var(--navy); font-size: 21px; }
  .card-back .brand-mark { left: 307px; top: 95px; width: 266px; height: 266px; border: 2px solid var(--gold); color: #fff; font-size: 26px; }

  .doctor-name { position: absolute; left: 62px; top: 288px; font-family: "Cinzel", serif; font-weight: 700; font-size: 29px; color: var(--navy); letter-spacing: 1px; }
  .doctor-title { position: absolute; left: 62px; top: 327px; font-size: 19px; color: var(--gold); }
  .divider { position: absolute; left: 62px; top: 361px; width: 765px; height: 1px; background: var(--rule); }

  .contact-list { position: absolute; left: 54px; top: 373px; list-style: none; font-size: 19px; color: var(--ink); }
  .contact-list li { display: flex; align-items: center; gap: 10px; height: 26px; }
  .contact-list svg { width: 18px; height: 18px; fill: var(--navy); }

  .address { position: absolute; right: 52px; top: 375px; text-align: right; font-size: 19px; line-height: 26px; color: var(--ink); font-style: normal; }

  .band-gold { position: absolute; left: 0; bottom: 0; width: 545px; height: 19px; background: var(--gold); }
  .band-navy { position: absolute; right: 0; bottom: 0; }
  .website { position: absolute; right: 52px; bottom: 8px; color: #fff; font-size: 19px; }

  .slogan { position: absolute; left: 0; right: 0; top: 430px; text-align: center; color: var(--gold); font-size: 19px; letter-spacing: 4px; }
</style>
</head>
<body>
  <section class="card card-front">
    <svg class="front-decor" width="480" height="500" role="img" aria-label="Faint background mark">
      <circle cx="190" cy="300" r="200" fill="var(--faint)"/>
    </svg>

    <div class="brand-mark">RV Bone &amp;<br>Vitality<br>Center</div>

    <h1 class="doctor-name">LYDIA VANCE, M.D.</h1>
    <p class="doctor-title">Board Certified Hand and Upper Extremity Surgeon</p>
    <div class="divider"></div>

    <ul class="contact-list">
      <li><svg viewBox="0 0 24 24"><path d="M6.6 10.8a15.1 15.1 0 0 0 6.6 6.6l2.2-2.2c.3-.3.7-.4 1-.2 1.1.4 2.3.6 3.6.6.6 0 1 .4 1 1V20c0 .6-.4 1-1 1A17 17 0 0 1 3 4c0-.6.4-1 1-1h3.5c.6 0 1 .4 1 1 0 1.3.2 2.5.6 3.6.1.3 0 .7-.2 1z"/></svg>954-218-4063</li>
      <li><svg viewBox="0 0 24 24"><path d="M6 2h9l3 3v4H6zM3 10h18v9H3zm3 6v6h12v-6z"/></svg>954-582-7341</li>
      <li><svg viewBox="0 0 24 24"><path d="M2 5h20v14H2zm2 2v.5l8 5 8-5V7z"/></svg>info@myrvbonecare.example</li>
    </ul>

    <address class="address">38517 North Willowmere Ave<br>Maple Harbor, FL 33958</address>

    <div class="band-gold"></div>
    <svg class="band-navy" width="350" height="42" viewBox="0 0 350 42"><polygon points="30,0 350,0 350,42 0,42" fill="var(--navy)"/></svg>
    <span class="website">www.myrvbonecare.example</span>
  </section>

  <section class="card card-back">
    <div class="brand-mark">RV Bone &amp;<br>Vitality<br>Center</div>
    <p class="slogan">STEADY HANDS. LASTING MOTION</p>
  </section>
</body>
</html>
```